New web design for a service provider in the medical field

We are looking for a new design for our website. We are a company that repairs and sells medical endoscopes. Our customers include doctors and hospitals. Our current website can be found at https://lumavex.de/en/lumavex-english.
We need a new web design (without programming) for the following 3 pages:
-Startpage https://lumavex.de/en/lumavex-english/
-Used endoscopes https://lumavex.de/en/used-endoscopes/
-Purchase https://lumavex.de/en/purchase/
The design should be modern and stylish.
The blue color of the logo should be reflected on the page, but not too intrusive.
I have uploaded the images from the header. If more images are needed, let me know and I will upload them.

Target Market(s)
Doctors and hospitals

```html
<!DOCTYPE html>
<html lang="en">
<head>
<meta charset="utf-8">
<title>Lumavex – Endoscope Repair &amp; Sales</title>
<link href="https://fonts.googleapis.com/css2?family=Rubik:wght@300;400;500;600;700&display=swap" rel="stylesheet">
<style>
:root{
  --blue:#0ba6e6;
  --blue-dark:#1b82c2;
  --ink:#16355a;
  --navy:#0f1a3a;
  --hero:#112a4e;
  --pale:#e8f5fc;
  --text:#5d6b7a;
  --orange:#ff9d0a;
  --white:#fff;
}
*{box-sizing:border-box;margin:0;padding:0}
html,body{width:1200px;height:3561px;overflow:hidden}
body{font-family:"Rubik",sans-serif;color:var(--ink);background:var(--white);position:relative}
.abs{position:absolute}
a{color:inherit;text-decoration:none}

/* top bar */
.topbar{left:0;top:0;width:1200px;height:28px;background:#f3fafd;font-size:9px;color:#333}
.topbar .tag{left:229px;top:9px}
.topbar .social{left:792px;top:9px;display:flex;gap:18px}
.dot{width:9px;height:9px;border-radius:50%;background:var(--blue);display:block}
.topbar .lang{left:917px;top:8px;display:flex;gap:6px;align-items:center}
.topbar .lang .dot{background:#c8102e}

/* header */
.header{left:0;top:28px;width:1200px;height:96px;background:var(--white)}
.brand{display:flex;align-items:center;gap:7px;font-weight:500;font-size:15px;color:var(--ink);white-space:nowrap}
.brand .mark{width:12px;height:12px;border-radius:50%;background:var(--blue)}
.header .brand{left:240px;top:26px}
.header .menu{left:434px;top:34px;display:flex;gap:32px;font-size:8px;color:#445;white-space:nowrap}
.contact{display:flex;gap:10px;align-items:center;white-space:nowrap}
.contact .ico{width:28px;height:28px;border-radius:50%;border:1px solid #8fd3f2;display:flex;align-items:center;justify-content:center}
.contact .lbl{font-size:7px;letter-spacing:1.5px;color:#333}
.contact .val{font-size:10px;color:#333}
.header .c1{left:671px;top:24px}
.header .c2{left:833px;top:24px}

/* nav */
.nav{left:229px;top:101px;width:741px;height:49px;background:var(--blue);z-index:3}
.nav ul{list-style:none;position:absolute;left:0;top:0;width:627px;height:49px;font-size:7.5px;font-weight:600;color:var(--white);white-space:nowrap}
.nav li{position:absolute;top:20px}
.nav .cta{position:absolute;right:0;top:0;width:114px;height:49px;background:#12304f;color:var(--white);font-size:11px;font-weight:600;display:flex;align-items:center;justify-content:center;white-space:nowrap}

/* hero */
.hero{left:0;top:124px;width:1200px;height:526px;background:radial-gradient(ellipse at 75% 45%,#2a5f8f 0%,#15355e 40%,#0b1b38 100%)}
.hero .eyebrow{left:229px;top:125px;font-size:11px;letter-spacing:3px;color:#dfe9f3}
.hero h1{left:226px;top:150px;font-size:47px;line-height:53px;font-weight:500;color:var(--white);white-space:nowrap}
.hero p{left:229px;top:271px;width:400px;font-size:10.5px;line-height:19px;color:#e4ecf4}
.btn{display:flex;align-items:center;justify-content:center;font-weight:600;white-space:nowrap}
.hero .btn{left:229px;top:360px;width:140px;height:48px;background:var(--blue);color:var(--white);font-size:11px}
.hero .arrows{left:229px;top:461px;display:flex;gap:8px}
.circle-btn{width:26px;height:26px;border-radius:50%;border:1px solid #9fb4cc;display:flex;align-items:center;justify-content:center}
.hero .pager{left:962px;top:246px;display:flex;flex-direction:column;gap:6px}
.hero .pager span{width:7px;height:7px;border-radius:50%;border:1px solid #cfdbe8}
.hero .pager span:first-child{background:#fff}

/* about */
.about{left:0;top:650px;width:1200px;height:580px;background:var(--pale)}
.photo-main{left:229px;top:76px;width:317px;height:380px;background:linear-gradient(135deg,#f2f4f6,#cfd4d8 60%,#9aa3aa)}
.photo-small{left:178px;top:326px;width:228px;height:180px;background:linear-gradient(160deg,#2d6d97,#173e61 70%,#0f2a44);box-shadow:0 10px 25px rgba(0,0,0,.2)}
.badge{left:508px;top:407px;width:70px;height:70px;border-radius:50%;background:var(--white);box-shadow:0 6px 18px rgba(0,0,0,.12);display:flex;align-items:center;justify-content:center}
.about h2{left:610px;top:90px;width:380px;font-size:19px;line-height:23px;font-weight:600;color:var(--blue-dark)}
.about .copy{left:611px;top:193px;width:365px;font-size:9px;line-height:15px;color:var(--text)}
.about .copy p{margin-bottom:15px}
.checks{left:610px;top:326px;list-style:none;font-size:9.5px;font-weight:600;color:var(--ink);white-space:nowrap}
.checks li{display:flex;gap:12px;align-items:center;height:25px}
.about .btn{left:610px;top:467px;width:126px;height:49px;background:var(--blue);color:var(--white);font-size:11px}

/* partners */
.partners{left:0;top:1230px;width:1200px;height:107px;background:#f2f9fd}
.partners .name{top:40px;font-size:25px;font-weight:700;letter-spacing:1px;color:var(--ink)}

/* services */
.services{left:0;top:1337px;width:1200px;height:623px;background:var(--white)}
.eyebrow-s{left:0;width:1200px;text-align:center;font-size:10px;letter-spacing:2.5px;color:#556}
.services .eyebrow-s{top:49px}
.services h2{left:0;top:67px;width:1200px;text-align:center;font-size:30px;font-weight:600;color:var(--ink)}
.card{top:134px;width:235px;height:416px;background:var(--white);box-shadow:0 4px 18px rgba(20,60,100,.09)}
.card .img{height:177px}
.card h3{position:absolute;left:12px;top:205px;font-size:18px;line-height:22px;font-weight:600;color:var(--blue-dark)}
.card p{position:absolute;left:13px;top:264px;width:205px;font-size:8.5px;line-height:15.5px;color:var(--text)}
.card .btn{position:absolute;left:13px;top:361px;width:209px;height:42px;background:var(--blue);color:var(--white);font-size:11px}

/* banner */
.banner{left:0;top:1960px;width:1200px;height:252px;background:linear-gradient(90deg,#39506d,#4a6384 50%,#3b5577)}
.trust{left:229px;top:2014px;width:361px;height:222px;background:var(--blue);z-index:2}
.trust .icon{position:absolute;left:50px;top:30px}
.trust p{position:absolute;left:46px;top:104px;font-size:22px;line-height:28px;color:var(--white);white-space:nowrap}
.banner h2{left:644px;top:46px;font-size:28px;line-height:36px;font-weight:600;color:var(--white)}
.banner .sub{left:644px;top:130px;font-size:18px;color:var(--white);white-space:nowrap}
.banner .btn{left:646px;top:177px;width:208px;height:42px;background:var(--orange);color:var(--white);font-size:11px}

/* why */
.why{left:0;top:2212px;width:1200px;height:657px;background:linear-gradient(180deg,#e3f3fc,#eef8fd 60%,#e6f4fc)}
.why h2{left:0;top:104px;width:1200px;text-align:center;font-size:22px;line-height:25px;font-weight:600;color:var(--ink)}
.feat{width:190px;text-align:center}
.feat svg{display:block;margin:0 auto 8px}
.feat h4{font-size:11px;font-weight:600;color:var(--blue-dark);margin-bottom:6px}
.feat p{font-size:8.5px;line-height:16.5px;color:var(--text)}
.why .btn{left:543px;top:558px;width:136px;height:41px;background:var(--blue);color:var(--white);font-size:11px}

/* cta */
.cta-band{left:0;top:2869px;width:1200px;height:322px;background:linear-gradient(180deg,#14a5e6,#0d95d6)}
.cta-band .eyebrow-s{top:72px;color:#e8f6ff}
.cta-band h2{left:0;top:88px;width:1200px;text-align:center;font-size:36px;font-weight:600;color:var(--white)}
.cta-band .sub{left:0;top:131px;width:1200px;text-align:center;font-size:30px;font-weight:300;color:var(--white)}
.cta-band .btn{left:530px;top:196px;width:141px;height:50px;background:var(--white);color:#122;font-size:11px}

/* footer */
.footer{left:0;top:3191px;width:1200px;height:370px;background:var(--navy);color:#d5dcea}
.footer .brand{left:239px;top:135px;color:var(--white)}
.footer h5{font-size:14px;font-weight:500;color:var(--white)}
.footer ul{list-style:none;font-size:9.5px;line-height:25.4px;margin-top:12px;white-space:nowrap}
.footer .col1{left:420px;top:74px}
.footer .col2{left:606px;top:72px}
.footer .contact .lbl,.footer .contact .val{color:var(--white)}
.footer .fc1{left:788px;top:75px}
.footer .fc2{left:788px;top:130px}
.footer .social{left:793px;top:196px;display:flex;gap:24px}
.footer .social .dot{background:#cfd8e6}
.footer .rule{left:229px;top:297px;width:741px;height:1px;background:#2c3a5e}
.footer .copy{left:0;top:327px;width:1200px;text-align:center;font-size:9.5px}
</style>
</head>
<body>

<div class="abs topbar">
  <span class="abs tag">Cause the outcome matters</span>
  <div class="abs social"><span class="dot"></span><span class="dot"></span><span class="dot"></span><span class="dot"></span></div>
  <div class="abs lang"><span class="dot"></span>English &gt;</div>
</div>

<header class="abs header">
  <div class="abs brand"><span class="mark"></span>Lumavex</div>
  <nav class="abs menu"><a>PICK-UP ORDER</a><a>ABOUT US</a><a>CONTACT US</a></nav>
  <div class="abs contact c1">
    <span class="ico"><svg width="14" height="12" viewBox="0 0 14 12"><rect x="1" y="1" width="12" height="10" fill="none" stroke="#0ba6e6"/><path d="M1 1l6 5 6-5" fill="none" stroke="#0ba6e6"/></svg></span>
    <div><div class="lbl">EMAIL</div><div class="val">info@lumavex.de</div></div>
  </div>
  <div class="abs contact c2">
    <span class="ico"><svg width="13" height="13" viewBox="0 0 24 24"><path d="M5 3l4 1 1 5-2 1a12 12 0 006 6l1-2 5 1 1 4-3 2C10 21 3 14 3 6z" fill="none" stroke="#0ba6e6" stroke-width="1.6"/></svg></span>
    <div><div class="lbl">PHONE</div><div class="val">+49 4151 555 017-0</div></div>
  </div>
</header>

<nav class="abs nav">
  <ul>
    <li style="left:19px">ENDOSCOPE REPAIR</li>
    <li style="left:125px">USED ENDOSCOPES</li>
    <li style="left:226px">ENDOSCOPY SYSTEMS</li>
    <li style="left:329px">ENDOSCOPY ACCESSORIES</li>
    <li style="left:459px">ACCESSORIES CATALOG</li>
    <li style="left:566px">PURCHASE</li>
  </ul>
  <a class="cta">Contact Now</a>
</nav>

<section class="abs hero" role="img" aria-label="Robotic surgical arms in a blue-lit operating theatre">
  <div class="abs eyebrow">YOUR FUTURE · OUR SERVICE</div>
  <h1 class="abs">Put Your Endoscope<br>in Relaible Hands !</h1>
  <p class="abs">Lumavex GmbH is specialised in the repair and sale of Koravia, Vestrel and Nimbara flexible medical endoscopes. As a service-oriented company, we are at your side with our knowledge and skills!</p>
  <a class="abs btn">Discover More</a>
  <div class="abs arrows">
    <span class="circle-btn"><svg width="8" height="8" viewBox="0 0 8 8"><path d="M5 1L2 4l3 3" fill="none" stroke="#cfdbe8"/></svg></span>
    <span class="circle-btn" style="border-color:#fff"><svg width="8" height="8" viewBox="0 0 8 8"><path d="M3 1l3 3-3 3" fill="none" stroke="#fff"/></svg></span>
  </div>
  <div class="abs pager"><span></span><span></span><span></span></div>
</section>

<section class="abs about">
  <div class="abs photo-main" role="img" aria-label="Hands holding an endoscope control body"></div>
  <div class="abs photo-small" role="img" aria-label="Robotic arm on a blue background"></div>
  <div class="abs badge"><svg width="36" height="36" viewBox="0 0 36 36"><circle cx="16" cy="16" r="12" fill="none" stroke="#5fc4ee" stroke-width="2"/><circle cx="16" cy="16" r="5" fill="none" stroke="#5fc4ee" stroke-width="2"/><path d="M20 20l10 10" stroke="#5fc4ee" stroke-width="2"/></svg></div>
  <h2 class="abs">Endoscope repairs and second hand endoscopes from Lumavex – cause the outcome matters!</h2>
  <div class="abs copy">
    <p>Lumavex is a privileged partner for the start-up facility or optimisation of existing healthcare facilities, doctor's offices and hospitals. The quality and reliability of our products and our offered service are our best advertisement!</p>
    <p>As a result of optimised processes and highly qualified specialists in our company, we can work very quickly and with high quality for your benefit of least possible restrictions in your doctor's office or in your hospital.</p>
  </div>
  <ul class="abs checks">
    <li><svg width="10" height="10" viewBox="0 0 10 10"><circle cx="5" cy="5" r="5" fill="#0ba6e6"/><path d="M2.5 5l2 2 3-3.5" fill="none" stroke="#fff" stroke-width="1.3"/></svg>One company for everyone</li>
    <li><svg width="10" height="10" viewBox="0 0 10 10"><circle cx="5" cy="5" r="5" fill="#0ba6e6"/><path d="M2.5 5l2 2 3-3.5" fill="none" stroke="#fff" stroke-width="1.3"/></svg>Experience Characterises Us</li>
    <li><svg width="10" height="10" viewBox="0 0 10 10"><circle cx="5" cy="5" r="5" fill="#0ba6e6"/><path d="M2.5 5l2 2 3-3.5" fill="none" stroke="#fff" stroke-width="1.3"/></svg>Guaranteed Service</li>
    <li><svg width="10" height="10" viewBox="0 0 10 10"><circle cx="5" cy="5" r="5" fill="#0ba6e6"/><path d="M2.5 5l2 2 3-3.5" fill="none" stroke="#fff" stroke-width="1.3"/></svg>Quality Not Quantity</li>
  </ul>
  <a class="abs btn">Learn More</a>
</section>

<section class="abs partners">
  <span class="abs name" style="left:340px">KORAVIA</span>
  <span class="abs name" style="left:538px">VESTREL</span>
  <span class="abs name" style="left:713px">NIMBARA</span>
</section>

<section class="abs services">
  <div class="abs eyebrow-s">OUR SERVICES</div>
  <h2 class="abs">What We Do</h2>
  <article class="abs card" style="left:229px">
    <div class="img" role="img" aria-label="Technician repairing an endoscope" style="background:linear-gradient(135deg,#eef0f2,#c9ced2 55%,#8fb9d4)"></div>
    <h3>Endoscope<br>Repair Service</h3>
    <p>Manufacturer-independent we repair and maintain endoscopes, individual components (e.g. processors or light sources), accessories and peripherals of the manufacturers Koravia, Vestrel and Nimbara.</p>
    <a class="btn">REPAIR REQUEST</a>
  </article>
  <article class="abs card" style="left:482px">
    <div class="img" role="img" aria-label="Endoscopy equipment with gauges" style="background:linear-gradient(135deg,#5d7893,#a9bccd 50%,#2a3f56)"></div>
    <h3>Sale Used<br>Endoscopes</h3>
    <p>Manufacturer-independent we repair and maintain endoscopes, individual components (e.g. processors or light sources), accessories and peripherals of the manufacturers Koravia, Vestrel and Nimbara.</p>
    <a class="btn">REPAIR REQUEST</a>
  </article>
  <article class="abs card" style="left:737px">
    <div class="img" role="img" aria-label="Coiled endoscope in a blue-lit room" style="background:linear-gradient(135deg,#3f86c4,#a8d3ee 55%,#dbeef9)"></div>
    <h3>Purchase Used<br>Endoscopes</h3>
    <p>Manufacturer-independent we repair and maintain endoscopes, individual components (e.g. processors or light sources), accessories and peripherals of the manufacturers Koravia, Vestrel and Nimbara.</p>
    <a class="btn">REPAIR REQUEST</a>
  </article>
</section>

<section class="abs banner" role="img" aria-label="Surgeons at work, tinted blue-grey">
  <h2 class="abs">Faulty<br>Endoscope ?</h2>
  <div class="abs sub">We ensure quick and smooth repairs!</div>
  <a class="abs btn">PICK-UP ORDER</a>
</section>
<div class="abs trust">
  <svg class="icon" width="54" height="54" viewBox="0 0 36 36"><circle cx="16" cy="16" r="12" fill="none" stroke="#fff" stroke-width="1.5"/><circle cx="16" cy="16" r="5" fill="none" stroke="#fff" stroke-width="1.5"/><path d="M20 20l10 10" stroke="#fff" stroke-width="1.5"/></svg>
  <p>We are trusted by<br>more than 250 Clients</p>
</div>

<section class="abs why">
  <h2 class="abs">Lumavex GmbH,<br>your decision for your future</h2>
  <div class="abs feat" style="left:260px;top:212px">
    <svg width="34" height="34" viewBox="0 0 34 34"><circle cx="17" cy="17" r="15" fill="none" stroke="#1b82c2" stroke-width="2"/><path d="M17 8v9l6 4" fill="none" stroke="#1b82c2" stroke-width="2"/></svg>
    <h4>Fast repairs</h4>
    <p>Keep potential disruptions in your doctor's office or in your hospital at minimum as a result of optimized processes and highly qualified specialists in our company</p>
  </div>
  <div class="abs feat" style="left:516px;top:212px">
    <svg width="34" height="34" viewBox="0 0 34 34"><path d="M4 16L17 4l13 12v15H21v-9h-8v9H4z" fill="none" stroke="#1b82c2" stroke-width="2"/></svg>
    <h4>On-site service</h4>
    <p>We will gladly pay you a visit to to carry out analysis and repairs on site. Due to our many years of experience – it doesn't get any faster (whigleithin a 250 km range)</p>
  </div>
  <div class="abs feat" style="left:784px;top:212px">
    <svg width="34" height="34" viewBox="0 0 34 34"><circle cx="17" cy="17" r="15" fill="none" stroke="#1b82c2" stroke-width="2"/><path d="M10 17l5 5 12-13" fill="none" stroke="#1b82c2" stroke-width="2"/></svg>
    <h4>Without a maintenance<br>contract</h4>
    <p>No subscription or other maintenance contract, but one-time and sustainable repair work</p>
  </div>
  <div class="abs feat" style="left:260px;top:396px">
    <svg width="34" height="34" viewBox="0 0 34 34"><path d="M8 3h13l6 6v22H8z" fill="none" stroke="#1b82c2" stroke-width="2"/><path d="M20 13h-4a2 2 0 000 4h2a2 2 0 010 4h-4M17 11v12" fill="none" stroke="#1b82c2" stroke-width="1.6"/></svg>
    <h4>Highly cost efficient</h4>
    <p>Benefit from our first class recommendations and implementation by our experienced staff. Our goals is to find the best solutions together with you at the best lowest price point.</p>
  </div>
  <div class="abs feat" style="left:516px;top:390px">
    <svg width="34" height="34" viewBox="0 0 34 34"><rect x="3" y="7" width="28" height="19" rx="2" fill="none" stroke="#1b82c2" stroke-width="2"/><path d="M3 13h28M15 22l4 4 8-8" fill="none" stroke="#1b82c2" stroke-width="2"/></svg>
    <h4>Loan equipment service</h4>
    <p>Use our service of high-quality loan devices during the downtime of your defective endoscope (limited to stock)</p>
  </div>
  <div class="abs feat" style="left:784px;top:390px">
    <svg width="34" height="34" viewBox="0 0 34 34"><path d="M4 15h6v16H4zM10 16l6-12c3 0 4 2 3 6l-1 4h10a2 2 0 012 3l-3 12a2 2 0 01-2 2H10" fill="none" stroke="#1b82c2" stroke-width="2"/></svg>
    <h4>First class service</h4>
    <p>Our clients always come first!</p>
  </div>
  <a class="abs btn">MORE ABOUT US</a>
</section>

<section class="abs cta-band">
  <div class="abs eyebrow-s">DON'T HESITATE TO CONTACT US</div>
  <h2 class="abs">How Can We Help You ?</h2>
  <div class="abs sub">Let's get started now</div>
  <a class="abs btn">Discover More</a>
</section>

<footer class="abs footer">
  <div class="abs brand"><span class="mark"></span>Lumavex</div>
  <div class="abs col1"><h5>About</h5><ul><li>INFORMATIONS</li><li>ABOUT US</li><li>CONTACT US</li><li>TOS</li><li>COPYRIGHTS</li><li>PRIVACY POLICY</li></ul></div>
  <div class="abs col2"><h5>Explore</h5><ul><li>ENDOSCOPE REPAIR</li><li>USED ENDOSCOPES</li><li>ENDOSCOPY SYSTEMS</li><li>ENDOSCOPY ACCESSORIES</li><li>ACCESSORIES CATALOG</li><li>PURCHASE</li></ul></div>
  <div class="abs contact fc1">
    <span class="ico"><svg width="14" height="12" viewBox="0 0 14 12"><rect x="1" y="1" width="12" height="10" fill="none" stroke="#0ba6e6"/><path d="M1 1l6 5 6-5" fill="none" stroke="#0ba6e6"/></svg></span>
    <div><div class="lbl">EMAIL</div><div class="val">info@lumavex.de</div></div>
  </div>
  <div class="abs contact fc2">
    <span class="ico"><svg width="13" height="13" viewBox="0 0 24 24"><path d="M5 3l4 1 1 5-2 1a12 12 0 006 6l1-2 5 1 1 4-3 2C10 21 3 14 3 6z" fill="none" stroke="#0ba6e6" stroke-width="1.6"/></svg></span>
    <div><div class="lbl">PHONE</div><div class="val">+49 4151 555 017-0</div></div>
  </div>
  <div class="abs social"><span class="dot"></span><span class="dot"></span><span class="dot"></span><span class="dot"></span></div>
  <div class="abs rule"></div>
  <div class="abs copy">© Copyright 2022 by lumavex</div>
</footer>

</body>
</html>
```